New Company Business Card design

Looking for a corporate looking business card utilising my new logo design - the logo i would like embossed as one option and flat as another - simplistic but stylish - less is more - we are an import export business launching into the market - i would like a couple of options as main background - Grey or Black

```html
<!DOCTYPE html>
<html lang="en">
<head>
<meta charset="utf-8">
<title>Northway Trade – Business Card Options</title>
<link rel="stylesheet" href="https://fonts.googleapis.com/css2?family=Crimson+Text:wght@400;600&display=swap">
<style>
  :root{
    --ink-dark:#333333;
    --brand-blue:#1173bc;
    --band-grey:#6d6e71;
    --paper:#f0f0f0;
    --panel:#d9d9d9;
    --text:#222222;
    --white:#ffffff;
    --tag-grey:#b8b9bb;
  }
  *{box-sizing:border-box;margin:0;padding:0}
  html,body{width:1200px;height:1200px;overflow:hidden;background:var(--white)}
  body{position:relative;font-family:"Crimson Text",Georgia,serif;color:var(--text)}

  .card{position:absolute;width:570px;height:340px;overflow:hidden}
  .card__art{position:absolute;inset:0;width:570px;height:340px;display:block}

  .option-divider{position:absolute;left:38px;top:629px;width:1129px;height:3px;background:#111}

  /* brand lockup */
  .brand{position:absolute;display:flex;flex-direction:column;align-items:center;width:300px}
  .brand__name{display:flex;align-items:center;gap:10px;color:var(--brand-blue);font-size:31px;font-weight:400;line-height:1;letter-spacing:.5px}
  .brand__dot{width:20px;height:20px;border-radius:50%;background:var(--brand-blue);flex:none}
  .brand__rule{display:flex;align-items:center;gap:6px;width:240px;margin-top:12px}
  .brand__rule::before,.brand__rule::after{content:"";flex:1;height:1px;background:var(--tag-grey)}
  .brand__tagline{color:var(--tag-grey);font-size:10px;letter-spacing:2.2px;text-transform:uppercase;white-space:nowrap}
  .brand--front{left:0;top:92px}
  .brand--back{left:136px;top:102px}

  /* contact rows */
  .contacts{list-style:none}
  .contact{position:absolute;left:383px;display:flex;align-items:center;gap:10px;font-size:19px;line-height:1;transform:translateY(-50%);color:var(--text)}
  .contact__icon{width:28px;height:24px;flex:none;display:block}
  .contact--phone{top:50px}
  .contact--web{top:116px}
  .contact--mail{top:191px}

  /* footer row */
  .card__footer{position:absolute;left:0;top:237px;width:570px;height:103px;display:flex;align-items:center}
  .card__footer--person{padding-left:30px;gap:34px}
  .card__footer--title{justify-content:center}
  .person-icon{width:52px;height:52px;flex:none}
  .footer-text{font-size:25px;letter-spacing:.3px;color:var(--text)}
  .card--blue-footer .footer-text{color:var(--white)}
</style>
</head>
<body>

<!-- Option 1 : grey footer, front -->
<section class="card card--front" style="left:17px;top:101px">
  <svg class="card__art" viewBox="0 0 570 340" aria-hidden="true">
    <rect width="570" height="340" fill="var(--paper)"/>
    <rect width="570" height="222" fill="var(--ink-dark)"/>
    <polygon points="290,0 570,0 570,222 353,222 293,150 350,150 299,80 345,80" fill="var(--brand-blue)"/>
    <polygon points="320,21 570,21 570,80 368,80" fill="var(--panel)"/>
    <polygon points="320,90 570,90 570,149 363,149" fill="var(--panel)"/>
    <polygon points="320,161 570,161 570,222 368,222" fill="var(--panel)"/>
    <rect y="222" width="570" height="15" fill="var(--band-grey)"/>
  </svg>
  <div class="brand brand--front">
    <div class="brand__name"><span class="brand__dot"></span>Northway Trade</div>
    <div class="brand__rule"></div>
    <div class="brand__tagline">Global goods for local markets</div>
  </div>
  <ul class="contacts">
    <li class="contact contact--phone">
      <svg class="contact__icon" viewBox="0 0 28 24"><circle cx="14" cy="12" r="11" fill="none" stroke="var(--brand-blue)" stroke-width="1.6"/><path d="M10.5 7.5c1-.6 1.6-.3 2 .6l.6 1.4c.2.6 0 1-.5 1.3l-.6.4c.4 1.3 1.3 2.4 2.4 3.1l.5-.5c.4-.4.9-.5 1.4-.2l1.3.8c.8.5.9 1.1.3 2-1.1 1.3-3 1.2-5-.6-2-1.9-3.4-4.4-2.4-8.3z" fill="var(--brand-blue)"/></svg>
      <span>++ 555 318</span>
    </li>
    <li class="contact contact--web">
      <svg class="contact__icon" viewBox="0 0 28 24"><rect x="1" y="3" width="26" height="12" rx="2" fill="none" stroke="var(--brand-blue)" stroke-width="1.3"/><text x="3.5" y="12" font-size="6.5" font-family="Arial,sans-serif" font-weight="700" fill="var(--brand-blue)">www://</text><path d="M17 13l6 3-2.4.8 2 3-1.3.8-2-3-1.8 1.6z" fill="var(--brand-blue)"/></svg>
      <span>northwaytrade.com</span>
    </li>
    <li class="contact contact--mail">
      <svg class="contact__icon" viewBox="0 0 28 24"><rect x="2" y="5" width="24" height="15" fill="var(--brand-blue)"/><path d="M2 5l12 9 12-9M2 20l9-7M26 20l-9-7" fill="none" stroke="var(--panel)" stroke-width="1.2"/></svg>
      <span>hello@nwtrade.com</span>
    </li>
  </ul>
  <div class="card__footer card__footer--person">
    <svg class="person-icon" viewBox="0 0 52 52" aria-hidden="true"><circle cx="26" cy="26" r="24.5" fill="none" stroke="#555" stroke-width="2"/><path d="M26 12c-5 0-7.5 3.6-7.5 8.3 0 4.2 2.4 8 4.6 9.3v2.2c-4.4 1.3-9 3-11.3 6.5M26 12c5 0 7.5 3.6 7.5 8.3 0 4.2-2.4 8-4.6 9.3v2.2c4.4 1.3 9 3 11.3 6.5" fill="none" stroke="#555" stroke-width="2"/></svg>
    <span class="footer-text">Mr. Ellis Marlow</span>
  </div>
</section>

<!-- Option 1 : grey footer, back -->
<section class="card card--back" style="left:609px;top:101px">
  <svg class="card__art" viewBox="0 0 570 340" aria-hidden="true">
    <rect width="570" height="340" fill="var(--paper)"/>
    <rect width="570" height="222" fill="var(--ink-dark)"/>
    <polygon points="0,0 111,150 46,150 103,222 0,222" fill="var(--brand-blue)"/>
    <rect y="222" width="570" height="15" fill="var(--band-grey)"/>
  </svg>
  <div class="brand brand--back">
    <div class="brand__name"><span class="brand__dot"></span>Northway Trade</div>
    <div class="brand__rule"></div>
    <div class="brand__tagline">Global goods for local markets</div>
  </div>
  <div class="card__footer card__footer--title">
    <span class="footer-text">Import Export Business Launching</span>
  </div>
</section>

<div class="option-divider"></div>

<!-- Option 2 : blue footer, front -->
<section class="card card--front card--blue-footer" style="left:17px;top:725px">
  <svg class="card__art" viewBox="0 0 570 340" aria-hidden="true">
    <rect width="570" height="340" fill="var(--brand-blue)"/>
    <rect width="570" height="222" fill="var(--ink-dark)"/>
    <polygon points="290,0 570,0 570,222 353,222 293,150 350,150 299,80 345,80" fill="var(--brand-blue)"/>
    <polygon points="320,21 570,21 570,80 368,80" fill="var(--panel)"/>
    <polygon points="320,90 570,90 570,149 363,149" fill="var(--panel)"/>
    <polygon points="320,161 570,161 570,222 368,222" fill="var(--panel)"/>
  </svg>
  <div class="brand brand--front">
    <div class="brand__name"><span class="brand__dot"></span>Northway Trade</div>
    <div class="brand__rule"></div>
    <div class="brand__tagline">Global goods for local markets</div>
  </div>
  <ul class="contacts">
    <li class="contact contact--phone">
      <svg class="contact__icon" viewBox="0 0 28 24"><circle cx="14" cy="12" r="11" fill="none" stroke="var(--brand-blue)" stroke-width="1.6"/><path d="M10.5 7.5c1-.6 1.6-.3 2 .6l.6 1.4c.2.6 0 1-.5 1.3l-.6.4c.4 1.3 1.3 2.4 2.4 3.1l.5-.5c.4-.4.9-.5 1.4-.2l1.3.8c.8.5.9 1.1.3 2-1.1 1.3-3 1.2-5-.6-2-1.9-3.4-4.4-2.4-8.3z" fill="var(--brand-blue)"/></svg>
      <span>++ 555 318</span>
    </li>
    <li class="contact contact--web">
      <svg class="contact__icon" viewBox="0 0 28 24"><rect x="1" y="3" width="26" height="12" rx="2" fill="none" stroke="var(--brand-blue)" stroke-width="1.3"/><text x="3.5" y="12" font-size="6.5" font-family="Arial,sans-serif" font-weight="700" fill="var(--brand-blue)">www://</text><path d="M17 13l6 3-2.4.8 2 3-1.3.8-2-3-1.8 1.6z" fill="var(--brand-blue)"/></svg>
      <span>northwaytrade.com</span>
    </li>
    <li class="contact contact--mail">
      <svg class="contact__icon" viewBox="0 0 28 24"><rect x="2" y="5" width="24" height="15" fill="var(--brand-blue)"/><path d="M2 5l12 9 12-9M2 20l9-7M26 20l-9-7" fill="none" stroke="var(--panel)" stroke-width="1.2"/></svg>
      <span>hello@nwtrade.com</span>
    </li>
  </ul>
  <div class="card__footer card__footer--person">
    <svg class="person-icon" viewBox="0 0 52 52" aria-hidden="true"><circle cx="26" cy="26" r="24.5" fill="none" stroke="var(--white)" stroke-width="2"/><path d="M26 12c-5 0-7.5 3.6-7.5 8.3 0 4.2 2.4 8 4.6 9.3v2.2c-4.4 1.3-9 3-11.3 6.5M26 12c5 0 7.5 3.6 7.5 8.3 0 4.2-2.4 8-4.6 9.3v2.2c4.4 1.3 9 3 11.3 6.5" fill="none" stroke="var(--white)" stroke-width="2"/></svg>
    <span class="footer-text">Mr. Ellis Marlow</span>
  </div>
</section>

<!-- Option 2 : blue footer, back -->
<section class="card card--back card--blue-footer" style="left:609px;top:725px">
  <svg class="card__art" viewBox="0 0 570 340" aria-hidden="true">
    <rect width="570" height="340" fill="var(--brand-blue)"/>
    <rect width="570" height="222" fill="var(--ink-dark)"/>
    <polygon points="0,0 111,150 46,150 103,222 0,222" fill="var(--brand-blue)"/>
    <rect y="222" width="570" height="15" fill="var(--panel)"/>
  </svg>
  <div class="brand brand--back">
    <div class="brand__name"><span class="brand__dot"></span>Northway Trade</div>
    <div class="brand__rule"></div>
    <div class="brand__tagline">Global goods for local markets</div>
  </div>
  <div class="card__footer card__footer--title">
    <span class="footer-text">Import Export Business Launching</span>
  </div>
</section>

</body>
</html>
```